Rig up a website for a Rigging Company

We already have a logo. Looking for a website design that works on pavlune.com.
Our rigging company uses semi trucks, forklifts, and similar equipment to move large machines.
Our logo is white, black and red.

Target Market(s)

Medical Industry (moving medical equipment), Utility Industry (power equipment), Food Industry (moving bottling/packing equipment), US Government (large equipment)

Industry/Entity Type

It Company

Coding

Coded - Design and coding required

Number of Pages Required

5+ page

Font styles to use
Sans Serif

Colors
ec1f27
ffffff
0355a3

Requirements
Must have
• Home page, About page, Services Page, and Contact Information page
Nice to have
• Pictures of semi and forklifts and ability to insert our own pictures of our equipment

```html
<!DOCTYPE html>
<html lang="en">
<head>
<meta charset="utf-8">
<title>Corvell Rigging</title>
<link rel="stylesheet" href="https://fonts.googleapis.com/css2?family=Roboto:wght@300;400;500;700&display=swap">
<style>
  :root {
    --red: #e8373c;
    --red-light: #f27a7a;
    --red-text: #e2262c;
    --white: #ffffff;
    --ink: #222222;
    --section-bg: #f1f1f1;
    --sky-top: #4f5560;
    --sky-glow: #d9c3a4;
    --sky-mid: #8f9097;
    --horizon: #b9b2a6;
    --ground-top: #5a616b;
    --ground: #2f353d;
  }
  * { box-sizing: border-box; margin: 0; padding: 0; }
  html, body { width: 1200px; height: 676px; overflow: hidden; background: var(--white); }
  body { font-family: "Roboto", sans-serif; color: var(--ink); }
  .page { position: relative; width: 1200px; height: 676px; overflow: hidden; }

  .hero {
    position: absolute; inset: 0 0 auto 0; height: 476px;
    background:
      radial-gradient(ellipse 520px 170px at 42% 44%, rgba(217,195,164,0.85) 0%, rgba(217,195,164,0) 100%),
      linear-gradient(180deg, var(--sky-top) 0%, var(--sky-mid) 38%, var(--horizon) 60%, var(--ground-top) 62%, var(--ground) 100%);
  }
  .site-header {
    position: absolute; top: 0; left: 0; right: 0; height: 72px;
    display: flex; align-items: center; padding: 0 40px 0 48px;
    border-bottom: 1px solid rgba(255,255,255,0.35);
  }
  .brand { display: flex; align-items: center; gap: 8px; font-weight: 700; font-size: 26px; color: var(--white); }
  .brand-mark { width: 12px; height: 12px; background: var(--red); }
  .main-nav { display: flex; gap: 38px; margin-left: 160px; }
  .main-nav a { color: var(--white); text-decoration: none; font-size: 15px; font-weight: 300; text-transform: uppercase; }
  .header-actions { margin-left: auto; display: flex; align-items: center; gap: 20px; }
  .phone { color: var(--white); font-size: 13px; font-weight: 500; }
  .quote-btn { background: var(--white); color: var(--ink); font-size: 13px; font-weight: 500; padding: 8px 14px; border-radius: 16px; text-decoration: none; }

  .welcome {
    position: absolute; top: 476px; left: 0; right: 0; height: 110px;
    background: linear-gradient(90deg, var(--red) 0%, var(--red-light) 100%);
    color: var(--white); text-align: center; padding-top: 12px;
  }
  .welcome h1 { font-size: 22px; font-weight: 700; }
  .divider-light { width: 1020px; margin: 10px auto 14px; border-top: 1px dashed rgba(255,255,255,0.85); }
  .welcome p { font-size: 13px; font-weight: 400; line-height: 1.55; width: 1020px; margin: 0 auto; }

  .services { position: absolute; top: 586px; left: 0; right: 0; bottom: 0; background: var(--section-bg); text-align: center; padding-top: 20px; }
  .services h2 { font-size: 22px; font-weight: 500; color: var(--ink); }
  .services h2 span { color: var(--red-text); }
  .divider-red { width: 1020px; height: 1px; margin: 14px auto 0; border: 0; border-top: 1px dashed #e2262c; }
</style>
</head>
<body>
<div class="page">
  <section class="hero" role="img" aria-label="Photo of a forklift carrying a wooden crate in front of a hangar at a harbour at dusk"></section>

  <header class="site-header">
    <div class="brand"><span class="brand-mark"></span>Corvell Rigging</div>
    <nav class="main-nav">
      <a href="#">Home</a>
      <a href="#">About Us</a>
      <a href="#">Services</a>
      <a href="#">Contact</a>
    </nav>
    <div class="header-actions">
      <span class="phone">+1 800 555 27 64</span>
      <a class="quote-btn" href="#">Request a Quote</a>
    </div>
  </header>

  <section class="welcome">
    <h1>Welcome to Corvell Rigging</h1>
    <div class="divider-light"></div>
    <p>Sed ut perspiciatis unde omnis iste natus error sit voluptatem accusantium doloremque laudantium, totam rem aperiam, eaque ipsa quae ab illo inventore veritatis et quasi architecto beatae vitae dicta sunt explicabo.</p>
  </section>

  <section class="services">
    <h2>Our <span>Services</span></h2>
    <div class="divider-red"></div>
  </section>
</div>
</body>
</html>
```